Fenwick Grading LTD - website for irrigation & Landscape Lighting & Buried service wire

Looking for a website to help promote my business with Irrigation (installation, service, etc) and buried service wire/drainage solutions.

Commercial/Residential

Landscape lighting.

I’ll get photos in the trucks and trailers to upload as well maybe the machine as well.

Target Market(s)

Homeowners who want green grass and beautiful gardens. Beautiful landscape lighting

Industry/Entity Type

Irrigation systems and landscape lighting and buried service wire to homes and offering Drainage soltions.

Coding

Coded - Design and coding required

Number of Pages Required

4 page

Colors
F0912C
F2A743
F7CA91
FBE8D2
FDF5EE

Requirements
Must have
• was hoping to link up my email on fenwickgrading@mailbox-example.net with the website if possible.
Nice to have
• Page for Irrigation, page for landscape lighting, page buried service wire & drainage soltions.

```html
<!DOCTYPE html>
<html lang="en">
<head>
<meta charset="utf-8">
<title>Trenching Services – Fenwick Grading LTD</title>
<link rel="stylesheet" href="https://fonts.googleapis.com/css2?family=Montserrat:wght@400;500;600;700&family=Roboto+Condensed:wght@700&display=swap">
<style>
:root{
  --orange:#F0912C;
  --orange-2:#F2A743;
  --orange-3:#F7CA91;
  --orange-4:#FBE8D2;
  --orange-5:#FDF5EE;
  --ink:#111111;
  --text:#4a4a4a;
  --white:#ffffff;
  --footer:#000000;
}
*{margin:0;padding:0;box-sizing:border-box}
html,body{width:1200px;height:4878px;overflow:hidden}
body{position:relative;background:var(--white);font-family:"Montserrat",sans-serif;color:var(--text)}

/* hero */
.hero{position:absolute;left:0;top:0;width:1200px;height:440px}
.hero-photo{position:absolute;inset:0;width:1200px;height:440px}
.brand{position:absolute;left:142px;top:24px;width:200px;display:flex;align-items:center;gap:10px;color:var(--white);font-weight:700;font-size:15px;line-height:19px;letter-spacing:.5px;text-transform:uppercase}
.brand-dot{flex:0 0 22px;width:22px;height:22px;border-radius:50%;background:var(--orange)}
.brand-name{display:block;width:150px}
.nav{position:absolute;top:32px;font-size:13px;color:var(--white);font-weight:500}
.nav a{position:absolute;white-space:nowrap;color:inherit;text-decoration:none}
.nav a.active{color:var(--orange);text-decoration:underline;text-underline-offset:4px}
.btn-contact{position:absolute;left:941px;top:23px;width:117px;height:37px;border-radius:19px;background:var(--orange);color:var(--white);font-size:11px;font-weight:600;display:flex;align-items:center;justify-content:center;letter-spacing:.5px}
.hero-title{position:absolute;left:142px;top:188px;font-family:"Roboto Condensed",sans-serif;font-size:36px;color:var(--white);font-weight:700}
.crumb{position:absolute;left:142px;top:232px;font-size:12px;color:var(--white)}
.crumb b{font-weight:700}

/* section headings */
.sec-title{position:absolute;left:0;width:1200px;text-align:center;font-family:"Roboto Condensed",sans-serif;font-weight:700;font-size:38px;color:var(--ink)}
.sec-title span{color:var(--orange)}
.sec-lead{position:absolute;text-align:center;font-size:12.5px;line-height:22.5px;color:var(--ink);font-weight:500}

/* feature rows */
.tri{position:absolute}
.item{position:absolute;width:425px}
.item h3{font-size:13px;font-weight:500;color:var(--ink);border-left:2px solid var(--orange);padding:8px 0 8px 11px;margin-bottom:24px}
.item p{font-size:12.5px;line-height:22.7px;color:var(--text)}

/* steps */
.step{position:absolute;width:210px;text-align:center}
.step-icon{width:86px;height:86px;border-radius:50%;background:var(--orange);margin:0 auto 34px;display:flex;align-items:center;justify-content:center}
.step h4{font-size:13px;font-weight:500;color:var(--ink);line-height:22px;margin-bottom:4px}
.step p{font-size:10px;line-height:17.6px;color:var(--text)}

/* footer */
.footer{position:absolute;left:0;top:4440px;width:1200px;height:438px}
.footer-brand{position:absolute;left:0;top:4565px;width:1200px;text-align:center;color:var(--white);font-weight:700;font-size:24px;text-transform:uppercase;letter-spacing:1px}
.footer-nav{position:absolute;top:4690px;font-size:12.5px;color:var(--white)}
.footer-nav a{position:absolute;white-space:nowrap;color:inherit;text-decoration:none}
.footer-nav a.active{color:var(--orange);font-weight:600}
.contact{position:absolute;top:4752px;display:flex;align-items:center;gap:14px;color:var(--white);font-size:12.5px;line-height:21px}
.contact-icon{width:34px;height:34px;border-radius:50%;background:var(--white);display:flex;align-items:center;justify-content:center}
.divider{position:absolute;left:142px;top:4814px;width:916px;height:1px;background:#3a3a3a}
.copy{position:absolute;left:142px;top:4835px;font-size:11.5px;color:var(--white)}
.social{position:absolute;top:4826px;width:32px;height:32px;border-radius:50%;border:1.5px solid var(--white)}
</style>
</head>
<body>

<header class="hero">
  <svg class="hero-photo" viewBox="0 0 1200 440" role="img" aria-label="Landscaped garden with lawn, shrubs, timber edging and a garden lamp">
    <defs>
      <linearGradient id="heroGrad" x1="0" y1="0" x2="1" y2="1">
        <stop offset="0" stop-color="#3f4a2c"/>
        <stop offset=".45" stop-color="#4c6b2a"/>
        <stop offset=".8" stop-color="#3d5a22"/>
        <stop offset="1" stop-color="#2e3a22"/>
      </linearGradient>
      <linearGradient id="heroShade" x1="0" y1="0" x2="0" y2="1">
        <stop offset="0" stop-color="#000" stop-opacity=".45"/>
        <stop offset=".6" stop-color="#000" stop-opacity=".15"/>
        <stop offset="1" stop-color="#000" stop-opacity="0"/>
      </linearGradient>
    </defs>
    <rect width="1200" height="440" fill="url(#heroGrad)"/>
    <rect width="1200" height="440" fill="url(#heroShade)"/>
    <path d="M0 360 L600 432 L1200 355 L1200 440 L0 440 Z" fill="#ffffff"/>
    <path d="M0 360 L600 432 L1200 355" fill="none" stroke="#F0912C" stroke-width="3"/>
  </svg>

  <div class="brand"><span class="brand-dot"></span><span class="brand-name">Fenwick Grading LTD</span></div>

  <nav class="nav">
    <a style="left:386px">Home</a>
    <a style="left:470px">Irrigation</a>
    <a style="left:574px">Landscape Lighting</a>
    <a class="active" style="left:748px">Fiber Optic Installation</a>
  </nav>
  <div class="btn-contact">CONTACT US</div>

  <h1 class="hero-title">Trenching&nbsp; Services</h1>
  <div class="crumb">Home » <b>Trenching&nbsp; Services</b></div>
</header>

<main>
  <h2 class="sec-title" style="top:528px">Trenching <span>Services</span></h2>
  <p class="sec-lead" style="left:165px;top:587px;width:870px">Trenching and buried service wire installations are common in various industries, including construction, telecommunications, and utilities. This method involves burying electrical or communication cables underground to provide a safer and&nbsp; more aesthetically pleasing solution compared to overhead installations. Here's a write-up that provides an overview of trenching and buried service wire installations</p>

  <svg class="tri" style="left:146px;top:755px" width="445" height="400" viewBox="0 0 445 400" role="img" aria-label="Smiling gardener holding a potted green plant">
    <defs><linearGradient id="g1" x1="0" y1="0" x2="1" y2="1"><stop offset="0" stop-color="#5c7a34"/><stop offset=".6" stop-color="#8aa056"/><stop offset="1" stop-color="#3c5524"/></linearGradient></defs>
    <polygon points="2,2 441,2 222,396" fill="none" stroke="#F0912C" stroke-width="1.5"/>
    <polygon points="2,2 434,2 218,386" fill="url(#g1)"/>
  </svg>
  <div class="item" style="left:640px;top:858px">
    <h3>Introduction</h3>
    <p>Trenching and buried service wire installations are crucial for creating durable and reliable underground infrastructure for electrical power distribution, communication networks, and other utility services. By burying cables, they are protected from environmental elements, accidental damage, and theft, while also improving the overall appearance of the space.</p>
  </div>

  <h2 class="sec-title" style="top:1231px">Trenching <span>Process</span></h2>
  <p class="sec-lead" style="left:250px;top:1289px;width:700px">The trenching process involves the excavation of a trench in the ground, where the cables will be placed. It generally follows a systematic approach</p>

  <svg class="tri" style="left:174px;top:1401px" width="332" height="294" viewBox="0 0 332 294" role="img" aria-label="Worker in a garden using a tablet for site planning">
    <defs><linearGradient id="g2" x1="0" y1="0" x2="1" y2="1"><stop offset="0" stop-color="#5f7a3a"/><stop offset=".5" stop-color="#9aaa78"/><stop offset="1" stop-color="#3f5a28"/></linearGradient></defs>
    <polygon points="2,2 330,2 166,291" fill="none" stroke="#F0912C" stroke-width="1.5"/>
    <polygon points="2,2 324,2 163,283" fill="url(#g2)"/>
  </svg>
  <div class="item" style="left:613px;top:1484px">
    <h3>Planning and Locating</h3>
    <p>Before initiating the trenching process, careful planning is required. This includes determining the type and size of cables to be installed, obtaining necessary permits, and identifying any existing utilities underground to avoid interference or damage.</p>
  </div>

  <div class="item" style="left:178px;top:1853px">
    <h3>Equipment and Excavation</h3>
    <p>Excavation of the trench is performed using various equipment, including backhoes, trenchers, or manual tools, depending on the scope and complexity of the project. The trench is typically dug to a specified depth and width, ensuring sufficient space for cable placement and appropriate depth for protection.</p>
  </div>
  <svg class="tri" style="left:696px;top:1779px" width="332" height="296" viewBox="0 0 332 296" role="img" aria-label="Garden tools and a hose laid out on green grass">
    <defs><linearGradient id="g3" x1="0" y1="0" x2="1" y2="1"><stop offset="0" stop-color="#2f6a2a"/><stop offset=".5" stop-color="#3f7d33"/><stop offset="1" stop-color="#2a5a24"/></linearGradient></defs>
    <polygon points="2,2 330,2 166,293" fill="none" stroke="#F0912C" stroke-width="1.5"/>
    <polygon points="2,2 324,2 163,285" fill="url(#g3)"/>
  </svg>

  <svg class="tri" style="left:174px;top:2160px" width="332" height="296" viewBox="0 0 332 296" role="img" aria-label="Person watering plants with a garden hose">
    <defs><linearGradient id="g4" x1="0" y1="0" x2="1" y2="1"><stop offset="0" stop-color="#566f3a"/><stop offset=".5" stop-color="#7d8d72"/><stop offset="1" stop-color="#3a4f2c"/></linearGradient></defs>
    <polygon points="2,2 330,2 166,293" fill="none" stroke="#F0912C" stroke-width="1.5"/>
    <polygon points="2,2 324,2 163,285" fill="url(#g4)"/>
  </svg>
  <div class="item" style="left:613px;top:2243px">
    <h3>Cable Installation</h3>
    <p>Upon excavating the trench, the cable is laid into the trench carefully. The specific cables required for the project, such as power cables or communication cables, are selected based on the needs and industry standards.</p>
  </div>

  <div class="item" style="left:178px;top:2565px">
    <h3>Backfilling and Compaction</h3>
    <p>Once the cables are appropriately placed, the trench is backfilled with suitable and compactable material, such as gravel, sand, or specialized backfill material. Proper compaction of the backfill material helps to prevent cable damage, maintain stability, and reduce the risk of future settlement.</p>
  </div>
  <svg class="tri" style="left:696px;top:2497px" width="332" height="296" viewBox="0 0 332 296" role="img" aria-label="Stone stepping path across a green lawn with trees">
    <defs><linearGradient id="g5" x1="0" y1="0" x2="1" y2="1"><stop offset="0" stop-color="#587a30"/><stop offset=".5" stop-color="#8aa86a"/><stop offset="1" stop-color="#4a7a2a"/></linearGradient></defs>
    <polygon points="2,2 330,2 166,293" fill="none" stroke="#F0912C" stroke-width="1.5"/>
    <polygon points="2,2 324,2 163,285" fill="url(#g5)"/>
  </svg>

  <h2 class="sec-title" style="top:2883px">Buried Service <span>Wire Installation</span></h2>
  <p class="sec-lead" style="left:175px;top:2942px;width:850px">Buried service wire installation refers to the specific process of burying cables that connect buildings or structures to the main power or communication networks. This includes residential homes, commercial buildings, or industrial sites. The steps involved in buried service wire installation typically include</p>

  <div class="step" style="left:147px;top:3071px">
    <div class="step-icon"><svg width="42" height="42" viewBox="0 0 42 42" fill="none" stroke="#fff" stroke-width="2"><circle cx="18" cy="24" r="12"/><path d="M18 24l7-7M30 6v8M26 10h8"/></svg></div>
    <h4>Site Assessment</h4>
    <p>The site is assessed to determine the most feasible path for the service wire installation, considering factors such as distance, terrain, existing infrastructure, and required permits.</p>
  </div>
  <div class="step" style="left:380px;top:3071px">
    <div class="step-icon"><svg width="42" height="42" viewBox="0 0 42 42" fill="none" stroke="#fff" stroke-width="2"><path d="M12 36V26a12 12 0 1 1 16 0v4h4"/><circle cx="21" cy="17" r="5"/></svg></div>
    <h4>Cable Routing</h4>
    <p>The route for the buried service wire is determined, ensuring it avoids obstacles and provides the most efficient and protected pathway.</p>
  </div>
  <div class="step" style="left:611px;top:3071px">
    <div class="step-icon"><svg width="42" height="42" viewBox="0 0 42 42" fill="none" stroke="#fff" stroke-width="2"><path d="M6 26h8l6 4h10M6 32h24"/><circle cx="24" cy="14" r="8"/><path d="M22 10h4M22 18h4"/></svg></div>
    <h4>Excavation and Cable Placement</h4>
    <p>Trenching is performed to create a trench along the determined route. The service wire is carefully laid into the trench, ensuring proper depth, alignment, and protection.</p>
  </div>
  <div class="step" style="left:843px;top:3071px">
    <div class="step-icon"><svg width="42" height="42" viewBox="0 0 42 42" fill="none" stroke="#fff" stroke-width="2"><path d="M6 24c4 0 8 6 10 10M36 24c-4 0-8 6-10 10"/><path d="M21 28V12M21 18c-4 0-6-4-6-8 4 0 6 3 6 8zM21 18c4 0 6-4 6-8-4 0-6 3-6 8z"/></svg></div>
    <h4>Backfilling and<br>Restoration</h4>
    <p>After the cable is placed and verified, the trench is backfilled and compacted to provide stability and protection. The area is then restored to its original condition, ensuring a seamless integration of the service wire installation.</p>
  </div>
</main>

<footer>
  <svg class="footer" viewBox="0 0 1200 438" aria-hidden="true">
    <path d="M0 84 L600 12 L1200 88 L1200 438 L0 438 Z" fill="#000"/>
    <path d="M0 84 L600 12 L1200 88" fill="none" stroke="#F0912C" stroke-width="4"/>
  </svg>
  <div class="footer-brand">Fenwick Grading LTD</div>
  <nav class="footer-nav">
    <a style="left:279px">Home</a>
    <a style="left:368px">Irrigation</a>
    <a style="left:478px">Landscape Lighting</a>
    <a class="active" style="left:656px">Fiber Optic Installation</a>
    <a style="left:852px;font-weight:600">Contact Us</a>
  </nav>

  <div class="contact" style="left:206px">
    <span class="contact-icon"><svg width="16" height="16" viewBox="0 0 24 24" fill="#000"><path d="M12 2a7 7 0 0 0-7 7c0 5 7 13 7 13s7-8 7-13a7 7 0 0 0-7-7zm0 9.5A2.5 2.5 0 1 1 12 6.5a2.5 2.5 0 0 1 0 5z"/></svg></span>
    <span>123, Building Name, Street<br>City, State XY 123456</span>
  </div>
  <div class="contact" style="left:528px">
    <span class="contact-icon"><svg width="16" height="16" viewBox="0 0 24 24" fill="#000"><path d="M6.6 10.8a15 15 0 0 0 6.6 6.6l2.2-2.2a1 1 0 0 1 1-.25 11 11 0 0 0 3.6.6 1 1 0 0 1 1 1V20a1 1 0 0 1-1 1A17 17 0 0 1 3 4a1 1 0 0 1 1-1h3.5a1 1 0 0 1 1 1 11 11 0 0 0 .6 3.6 1 1 0 0 1-.25 1z"/></svg></span>
    <span>Phone<br>123-456-7890</span>
  </div>
  <div class="contact" style="left:765px">
    <span class="contact-icon"><svg width="15" height="15" viewBox="0 0 24 24" fill="#000"><path d="M2 5h20v14H2z" fill="none" stroke="#000" stroke-width="2"/><path d="M2 5l10 8 10-8" fill="none" stroke="#000" stroke-width="2"/></svg></span>
    <span>E-Mail<br>info@fenwickgrading-example.net</span>
  </div>

  <div class="divider"></div>
  <div class="copy">© 2024 Fenwick Grading LTD . All Rights Reserved.</div>
  <span class="social" style="left:906px" aria-label="Social profile"></span>
  <span class="social" style="left:946px" aria-label="Social profile"></span>
  <span class="social" style="left:985px" aria-label="Social profile"></span>
  <span class="social" style="left:1025px" aria-label="Social profile"></span>
</footer>

</body>
</html>
```